Coach Bruno Velasque Life Coach webpage

I am a Triathlon Coach but now I am in the process of opening a "new brand" as a Life Coach therefore I need new image and a new webpage. I live in Mexico city and would like to offer my services to Latinamerican clientes (spanish speaking). My actual website is www.trenquo.mx. My new website should help me to communicate what I do (Life Coaching), how my services are different from others, help gain new clients through one on one sessions, and I also offer a mental training course. I would like to see designs from a ZEN perspective (minimalistic, light and peaceful colors and not strong colors like my current webpage). The final design should communicate a sense of peace, tranquility, accomplishment and accompaniment. I would like to be able to manipulate the information and add-ons such a section were people can buy, subscribe and pay for the courses.

Target Market(s)

Male and female between 35 and 60 years who are going through changes in their life, need to make important decisions (such a divorcing or not, quitting or changing jobs, or not, etc), and or who do not fell happy with their current life.

Industry/Entity Type

Coaching

Coding

Coded - Design and coding required

Number of Pages Required

5+ page

Font styles to use
Sans Serif

Colors

Designer to choose colors to be used in the design.

Requirements
Must have
• 6 sections and one of those sections a place where my clients can buy courses and pay for them there. I would like to be able to change some of the information easily. I would like to see designs from a ZEN perspective (minimalistic, light and peaceful colors and not strong colors like my current webpage). The final design should communicate a sense of peace, tranquility, accomplishment and accompaniment. I would like to be able to manipulate the informati
Should not have
• dark strong colors

```html
<!DOCTYPE html>
<html lang="en">
<head>
<meta charset="utf-8">
<title>Bruno Velasque — Life Coach</title>
<link rel="stylesheet" href="https://fonts.googleapis.com/css2?family=Cinzel:wght@500;600;700&family=Outfit:wght@300;400;500;600&family=Roboto:wght@400;500&display=swap">
<style>
:root{
  --sage:#7d9a93;
  --sage-dark:#6c8880;
  --footer:#4f6762;
  --mint:#e2efec;
  --mint-faq:#ddece6;
  --olive:#b3bb26;
  --ink:#1f3d48;
  --text:#2f3a3c;
  --white:#ffffff;
}
*{box-sizing:border-box;margin:0;padding:0}
html,body{width:1200px;height:4370px;overflow:hidden}
body{position:relative;font-family:"Outfit",sans-serif;color:var(--text);background:var(--white)}
.abs{position:absolute}
.btn{position:absolute;background:var(--olive);color:var(--white);font-size:14px;display:flex;align-items:center;justify-content:center;white-space:nowrap}
.btn-outline{position:absolute;border:2px solid var(--ink);color:var(--ink);font-size:14px;display:flex;align-items:center;justify-content:center;background:var(--white)}
.section-title{position:absolute;left:0;width:1200px;text-align:center;font-family:"Cinzel",serif;font-weight:600;font-size:50px;color:var(--ink);letter-spacing:1px;white-space:nowrap}
.para{position:absolute;font-size:13.5px;line-height:24px;text-align:justify;color:var(--text)}

/* hero */
.hero{position:absolute;left:0;top:0;width:1200px;height:604px;background:linear-gradient(180deg,#829f98 0%,#7b978f 60%,#6f8c85 100%)}
.logo{position:absolute;font-family:"Cinzel",serif;font-weight:600;color:var(--white);white-space:nowrap}
.nav a{position:absolute;top:32px;color:var(--white);font-size:14px;text-decoration:none;white-space:nowrap}
.nav .active::before{content:"";position:absolute;left:-2px;right:-2px;top:-32px;height:4px;background:var(--white)}
.welcome{left:143px;top:160px;color:var(--white);font-size:14px;font-weight:500;font-family:"Roboto",sans-serif}
.hero-title{left:143px;top:186px;color:var(--white);font-family:"Cinzel",serif;font-weight:600;font-size:41px;white-space:nowrap}
.ticks{position:absolute;left:143px;top:252px;list-style:none}
.ticks li{height:30.5px;display:flex;align-items:center;color:var(--white);font-size:13.5px;white-space:nowrap}
.ticks svg{margin-right:12px}
.arrow{position:absolute;top:482px;width:30px;height:30px;border-radius:50%;background:#e9eeec;display:flex;align-items:center;justify-content:center}
.hero-photo{left:611px;top:100px;width:433px;height:504px;border-radius:40px 90px 0 90px;background:radial-gradient(circle at 48% 30%,#f6c060 0%,#d4772c 25%,#8a4a22 55%,#2e2420 100%)}

/* about */
.about-circle{left:119px;top:984px;width:142px;height:142px;border-radius:50%;background:var(--olive)}
.about-photo{left:144px;top:696px;width:433px;height:402px;border-radius:0 90px 0 0;background:linear-gradient(160deg,#a9b68c 0%,#6c7f56 40%,#34506e 75%,#2a3340 100%)}

/* services */
.services{position:absolute;left:0;top:1201px;width:1200px;height:708px;background:var(--mint)}
.card{position:absolute;top:1368px;width:440px;height:419px;background:var(--white)}
.card .icon{position:absolute;left:31px;top:20px;width:122px;height:122px;border-radius:50%;background:var(--olive)}
.card h3{position:absolute;left:166px;top:40px;font-size:28px;font-weight:600;line-height:41px;color:var(--ink)}
.card .para{left:41px;top:160px;width:360px}

/* blog */
.post{position:absolute;top:2084px;width:284px}
.post .pic{height:195px}
.post .date{margin:12px 0 0 16px;font-size:14px;display:flex;align-items:center;gap:7px}
.post h4{margin:6px 0 0 16px;font-size:18px;font-weight:600;color:var(--ink)}
.post p{margin:4px 12px 0 16px;font-size:13.5px;line-height:24px;text-align:justify}

/* contact */
.contact{position:absolute;left:0;top:2545px;width:1200px;height:747px;background:linear-gradient(180deg,#6f8a83,#6a857e)}
.contact-photo{left:143px;top:2715px;width:432px;height:468px;border-radius:0 80px 0 80px;background:linear-gradient(180deg,#c9c2b3 0%,#a9a79c 45%,#8d948f 70%,#5b5f58 100%)}
.field{position:absolute;left:599px;width:457px;border:2px solid #e8eeec;border-radius:28px;color:#eef3f1;font-size:14px;padding-left:28px;display:flex;align-items:center}
.field.msg{align-items:flex-start;padding-top:16px;border-radius:34px}

/* faq */
.faq{position:absolute;left:256px;width:688px;height:55px;background:var(--mint-faq);display:flex;align-items:center;padding-left:21px;font-size:17.5px;color:var(--text)}
.faq .plus{position:absolute;right:14px;top:9px;width:38px;height:38px;border-radius:50%;background:var(--olive);color:var(--white);display:flex;align-items:center;justify-content:center;font-size:16px}

/* footer */
.footer{position:absolute;left:0;top:3988px;width:1200px;height:382px;background:var(--footer);color:var(--white)}
.social{position:absolute;top:4131px;width:40px;height:40px;border-radius:50%;background:#5f7670}
.social.on{background:var(--white)}
.info{position:absolute;left:462px;font-size:13px;color:var(--white)}
.info b{display:block;font-size:15px;font-weight:500;margin-bottom:6px}
.qlinks{position:absolute;top:4122px;list-style:none;font-size:15px}
.qlinks li{height:32px;display:flex;align-items:center;gap:14px;white-space:nowrap}
.copy{position:absolute;left:0;width:1200px;top:4330px;text-align:center;font-size:14px;font-weight:500}
</style>
</head>
<body>

<!-- Hero -->
<header class="hero">
  <div class="logo" style="left:143px;top:22px;font-size:22px">BRUNO VELASQUE</div>
  <nav class="nav">
    <a class="active" style="left:543px">Home</a>
    <a style="left:609px">About</a>
    <a style="left:679px">Services</a>
    <a style="left:762px">Blog</a>
    <a style="left:821px">Contact</a>
  </nav>
  <div class="btn" style="left:935px;top:20px;width:121px;height:41px">Get A Quote</div>
  <div class="abs welcome">WELCOME TO</div>
  <h1 class="abs hero-title">BRUNO VELASQUE</h1>
  <ul class="ticks">
    <li><svg width="14" height="14" viewBox="0 0 14 14"><circle cx="7" cy="7" r="7" fill="#fff"/><path d="M4 7.2l2 2 4-4.2" stroke="#7d9a93" stroke-width="1.8" fill="none"/></svg>Lorem ipsum dolor sit amet, consectetur adipiscing</li>
    <li><svg width="14" height="14" viewBox="0 0 14 14"><circle cx="7" cy="7" r="7" fill="#fff"/><path d="M4 7.2l2 2 4-4.2" stroke="#7d9a93" stroke-width="1.8" fill="none"/></svg>Lorem ipsum dolor sit amet, consectetur adipiscing</li>
    <li><svg width="14" height="14" viewBox="0 0 14 14"><circle cx="7" cy="7" r="7" fill="#fff"/><path d="M4 7.2l2 2 4-4.2" stroke="#7d9a93" stroke-width="1.8" fill="none"/></svg>Lorem ipsum dolor sit amet, consectetur adipiscing</li>
    <li><svg width="14" height="14" viewBox="0 0 14 14"><circle cx="7" cy="7" r="7" fill="#fff"/><path d="M4 7.2l2 2 4-4.2" stroke="#7d9a93" stroke-width="1.8" fill="none"/></svg>Lorem ipsum dolor sit amet, consectetur adipiscing</li>
  </ul>
  <div class="btn" style="left:143px;top:384px;width:273px;height:40px">Schedule A Free Consultation Session</div>
  <div class="arrow" style="left:143px"><svg width="10" height="10" viewBox="0 0 10 10"><path d="M6.5 1.5L3 5l3.5 3.5" stroke="#333" stroke-width="1.6" fill="none"/></svg></div>
  <div class="arrow" style="left:184px"><svg width="10" height="10" viewBox="0 0 10 10"><path d="M3.5 1.5L7 5 3.5 8.5" stroke="#333" stroke-width="1.6" fill="none"/></svg></div>
  <div class="abs hero-photo" role="img" aria-label="Photo of a woman raising her hands toward the sunset over mountains"></div>
</header>

<!-- About -->
<section>
  <div class="abs about-circle"></div>
  <div class="abs about-photo" role="img" aria-label="Portrait photo of a smiling grey-haired coach in a denim jacket outdoors"></div>
  <h2 class="abs" style="left:616px;top:684px;font-family:'Cinzel',serif;font-weight:600;font-size:50px;color:var(--ink)">ABOUT ME</h2>
  <p class="para" style="left:616px;top:752px;width:440px">Lorem ipsum dolor sit amet, consectetur adipiscing elit, sed do eiusmod tempor incididunt ut labore et dolore magna aliqua. Ut enim ad minim veniam, quis nostrud exercitation ullamco laboris nisi ut aliquip ex ea commodo consequat. Duis aute irure dolor in reprehenderit in voluptate velit esse cillum dolore eu fugiat nulla pariatur. Excepteur sint occaecat cupidatat non proident, sunt in culpa qui officia deserunt mollit anim id est laborum. Lorem ipsum dolor sit amet, consectetur adipiscing elit, sed do eiusmod tempor incididunt ut labore et dolore magna aliqua. Ut enim ad minim veniam, quis nostrud exercitation ullamco laboris nisi ut aliquip ex ea commodo consequat. Duis aute irure dolor in reprehenderit in voluptate velit esse cillum dolore eu fugiat nulla pariatur.</p>
  <div class="btn" style="left:616px;top:1056px;width:121px;height:42px">Learn More</div>
</section>

<!-- Services -->
<section class="services"></section>
<h2 class="section-title" style="top:1284px">OUR SERVICES</h2>
<article class="card" style="left:144px">
  <div class="icon" role="img" aria-label="Life coaching icon"></div>
  <h3>Personalized<br>Life Coaching</h3>
  <p class="para">Lorem ipsum dolor sit amet, consectetur adipiscing elit, sed do eiusmod tempor incididunt ut labore et dolore magna aliqua. Ut enim ad minim veniam, quis nostrud exercitation ullamco laboris nisi ut aliquip ex ea commodo consequat. Duis aute irure dolor in reprehenderit in voluptate velit esse cillum dolore eu fugiat nulla pariatur.</p>
  <div class="btn-outline" style="left:41px;top:344px;width:121px;height:41px">Learn More</div>
</article>
<article class="card" style="left:614px">
  <div class="icon" role="img" aria-label="Mental training icon"></div>
  <h3>Mental Training<br>Courses</h3>
  <p class="para">Lorem ipsum dolor sit amet, consectetur adipiscing elit, sed do eiusmod tempor incididunt ut labore et dolore magna aliqua. Ut enim ad minim veniam, quis nostrud exercitation ullamco laboris nisi ut aliquip ex ea commodo consequat. Duis aute irure dolor in reprehenderit in voluptate velit esse cillum dolore eu fugiat nulla pariatur.</p>
  <div class="btn-outline" style="left:41px;top:344px;width:121px;height:41px">Learn More</div>
</article>

<!-- Blog -->
<h2 class="section-title" style="top:1988px">LATEST BLOG</h2>
<article class="post" style="left:143px">
  <div class="pic" role="img" aria-label="Photo of a coach speaking to a group in a bright room" style="background:linear-gradient(135deg,#d9dcd7,#b9a98e 50%,#8f8d86)"></div>
  <div class="date"><svg width="14" height="14" viewBox="0 0 14 14"><rect x="1" y="2.5" width="12" height="10.5" rx="1" fill="none" stroke="#333" stroke-width="1.4"/><path d="M1 6h12M4 1v3M10 1v3" stroke="#333" stroke-width="1.4"/></svg>Jan 20, 2024</div>
  <h4>Lorem ipsum dolor sit amet</h4>
  <p>Lorem ipsum dolor sit amet, consectetur adipiscing elit, sed do eiusmod tempor incididunt ut labore et dolore magna aliqua.</p>
</article>
<article class="post" style="left:458px">
  <div class="pic" role="img" aria-label="Photo of a support group sitting in a circle" style="background:linear-gradient(135deg,#c7c0ad,#8d7b63 50%,#5e5a52)"></div>
  <div class="date"><svg width="14" height="14" viewBox="0 0 14 14"><rect x="1" y="2.5" width="12" height="10.5" rx="1" fill="none" stroke="#333" stroke-width="1.4"/><path d="M1 6h12M4 1v3M10 1v3" stroke="#333" stroke-width="1.4"/></svg>Jan 20, 2024</div>
  <h4>Lorem ipsum dolor sit amet</h4>
  <p>Lorem ipsum dolor sit amet, consectetur adipiscing elit, sed do eiusmod tempor incididunt ut labore et dolore magna aliqua.</p>
</article>
<article class="post" style="left:772px">
  <div class="pic" role="img" aria-label="Photo of a woman holding a tablet outside an office building" style="background:linear-gradient(135deg,#3d4245,#6d6a63 50%,#c9c1b3)"></div>
  <div class="date"><svg width="14" height="14" viewBox="0 0 14 14"><rect x="1" y="2.5" width="12" height="10.5" rx="1" fill="none" stroke="#333" stroke-width="1.4"/><path d="M1 6h12M4 1v3M10 1v3" stroke="#333" stroke-width="1.4"/></svg>Jan 20, 2024</div>
  <h4>Lorem ipsum dolor sit amet</h4>
  <p>Lorem ipsum dolor sit amet, consectetur adipiscing elit, sed do eiusmod tempor incididunt ut labore et dolore magna aliqua.</p>
</article>

<!-- Contact -->
<section class="contact"></section>
<h2 class="section-title" style="top:2628px;color:var(--white)">CONTACT US</h2>
<div class="abs contact-photo" role="img" aria-label="Photo of a woman sitting on a sofa looking at her phone"></div>
<div class="field" style="top:2722px;height:54px">Your name</div>
<div class="field" style="top:2793px;height:55px">Email</div>
<div class="field" style="top:2866px;height:55px">Phone</div>
<div class="field msg" style="top:2939px;height:185px">Message</div>
<div class="btn" style="left:606px;top:3141px;width:120px;height:42px">Submit Now</div>

<!-- FAQ -->
<h2 class="section-title" style="top:3370px;font-size:44px">FREQUENTLY ASKED QUESTIONS</h2>
<div class="faq" style="top:3455px">Lorem ipsum dolor sit amet, consectetur adipiscing elit<span class="plus">+</span></div>
<div class="faq" style="top:3535px">Lorem ipsum dolor sit amet, consectetur adipiscing elit<span class="plus">+</span></div>
<div class="faq" style="top:3615px">Lorem ipsum dolor sit amet, consectetur adipiscing elit<span class="plus">+</span></div>
<div class="faq" style="top:3695px">Lorem ipsum dolor sit amet, consectetur adipiscing elit<span class="plus">+</span></div>
<div class="faq" style="top:3775px">Lorem ipsum dolor sit amet, consectetur adipiscing elit<span class="plus">+</span></div>
<div class="btn" style="left:528px;top:3854px;width:144px;height:42px">View More Faq's</div>

<!-- Footer -->
<footer class="footer"></footer>
<div class="logo" style="left:141px;top:4072px;font-size:25px">BRUNO VELASQUE</div>
<div class="social" style="left:145px"></div>
<div class="social on" style="left:194px"></div>
<div class="social" style="left:241px"></div>

<h5 style="position:absolute;left:462px;top:4066px;font-size:20px;font-weight:600;color:#fff;letter-spacing:.5px">CONTACT INFO</h5>
<div class="info" style="top:4122px">
  <svg class="abs" style="left:0;top:2px" width="12" height="16" viewBox="0 0 12 16"><path d="M6 0a6 6 0 0 0-6 6c0 4.5 6 10 6 10s6-5.5 6-10a6 6 0 0 0-6-6z" fill="#fff"/><circle cx="6" cy="6" r="2.2" fill="#4f6762"/></svg>
  <div style="margin-left:42px"><b>Address :</b>123, Lorem ipsum dolor sit</div>
</div>
<div class="info" style="top:4178px">
  <svg class="abs" style="left:0;top:3px" width="18" height="13" viewBox="0 0 18 13"><rect width="18" height="13" rx="1" fill="#fff"/><path d="M0 1l9 6 9-6" stroke="#4f6762" stroke-width="1.4" fill="none"/></svg>
  <div style="margin-left:42px"><b>Email</b>hola@calmavia.mx</div>
</div>
<div class="info" style="top:4234px">
  <svg class="abs" style="left:0;top:2px" width="16" height="16" viewBox="0 0 16 16"><path d="M3.5 0.5l3 3-2 2.2c1 2.2 2.6 3.8 4.8 4.8l2.2-2 3 3-2 2.5C7 13.5 2.5 9 0.5 3.5z" fill="#fff"/></svg>
  <div style="margin-left:42px"><b>Phone</b>1-800-555-0142</div>
</div>

<h5 style="position:absolute;left:747px;top:4066px;font-size:20px;font-weight:600;color:#fff;letter-spacing:.5px">QUICK LINKS</h5>
<ul class="qlinks" style="left:747px;color:#fff">
  <li>»<span>Home</span></li><li>»<span>About</span></li><li>»<span>Services</span></li><li>»<span>Contact</span></li>
</ul>
<ul class="qlinks" style="left:881px;color:#fff">
  <li>»<span>Terms and Condition</span></li><li>»<span>Privacy policy</span></li><li>»<span>Help</span></li><li>»<span>Support</span></li>
</ul>
<div class="copy" style="color:#fff">© Copyrights 2024 | All Rights Reserved</div>

</body>
</html>
```